Business Card Design

Velora Pixel Outreach

An online marketing consulting & strategy business for the cosmetic niche

We specialise in Increasing Leads, Conversions & Content Marketing

I am looking for a very clean, BOLD business card that is simple & effective

Target Market(s)

cosmetic surgeons & cosmetic clinics

Industry/Entity Type

Marketing

Contact Information for Business Card

Dermot Kalway
Online Marketing Strategist

Dermot@VeloraPixelOutreach.example
0492 158 620

LinkedIn: in/dermotkalway

```html
<!DOCTYPE html>
<html lang="en">
<head>
<meta charset="utf-8">
<title>Velora Pixel Outreach — Business Cards</title>
<link rel="stylesheet" href="https://fonts.googleapis.com/css2?family=Exo+2:wght@500&family=Roboto:wght@400;500&display=swap">
<style>
  :root {
    --board: #a9a7a7;
    --card-white: #ffffff;
    --card-black: #050505;
    --brand-blue: #29a9e0;
    --brand-green: #9dcb3b;
    --mark-teal: #1fb5c9;
    --wordmark-grey: #666666;
    --text-white: #ffffff;
    --card-shadow: rgba(0,0,0,0.35);
  }
  * { margin: 0; padding: 0; box-sizing: border-box; }
  html, body { width: 1200px; height: 900px; overflow: hidden; background: var(--board); }
  .board { position: relative; width: 1200px; height: 900px; }

  .card {
    position: absolute;
    width: 567px; height: 342px;
    background: var(--card-white);
    overflow: hidden;
    box-shadow: 2px 3px 4px var(--card-shadow);
  }
  .card--rounded { border-radius: 22px; height: 327px; }
  .card--front.card--top { left: 18px; top: 108px; }
  .card--back.card--top { left: 612px; top: 108px; }
  .card--front.card--bottom { left: 18px; top: 485px; }
  .card--back.card--bottom { left: 612px; top: 485px; }

  .card__waves { position: absolute; inset: 0; width: 100%; height: 100%; }
  .wave-blue { fill: var(--brand-blue); }
  .wave-green { fill: var(--brand-green); }
  .wave-black { fill: var(--card-black); }

  .brand-dot { position: absolute; border-radius: 50%; background: var(--mark-teal); }
  .card--front .brand-dot { left: 40px; top: 12px; width: 150px; height: 150px; }
  .brand-dot--faint { opacity: 0.15; left: 230px !important; top: -20px !important; width: 320px !important; height: 320px !important; background: var(--brand-blue); }
  .card--back .brand-dot { left: 22px; top: 40px; width: 64px; height: 64px; }

  .front-wordmark {
    position: absolute; left: 0; width: 100%;
    text-align: center;
    font-family: "Exo 2", sans-serif; font-weight: 500;
    color: var(--text-white);
    font-size: 39px; line-height: 35px; letter-spacing: 3px;
    text-transform: uppercase;
  }
  .card--top .front-wordmark { top: 205px; }
  .card--bottom .front-wordmark { top: 196px; }

  .back-wordmark {
    position: absolute; left: 106px; top: 38px;
    font-family: "Exo 2", sans-serif; font-weight: 500;
    color: var(--wordmark-grey);
    font-size: 27px; line-height: 25px; letter-spacing: 2.5px;
    text-transform: uppercase;
  }

  .person { position: absolute; left: 22px; font-family: Roboto, Arial, sans-serif; }
  .card--top .person { top: 226px; }
  .card--bottom .person { top: 214px; }
  .person__name { font-size: 23px; font-weight: 500; line-height: 28px; }
  .person__first { color: var(--brand-blue); }
  .person__last { color: var(--brand-green); }
  .person__role { font-size: 15px; font-weight: 500; color: var(--brand-green); margin-top: 2px; }

  .contact-list { position: absolute; left: 260px; list-style: none; font-family: Roboto, Arial, sans-serif; }
  .card--top .contact-list { top: 229px; }
  .card--bottom .contact-list { top: 217px; }
  .contact-list__item {
    display: flex; align-items: center; gap: 10px;
    height: 20px; margin-bottom: 15px;
    color: var(--text-white); font-size: 14.5px;
  }
  .contact-icon { width: 20px; height: 20px; flex: none; }
</style>
</head>
<body>
<main class="board">

  <!-- Front, square corners -->
  <section class="card card--front card--top" aria-label="Card front">
    <div class="brand-dot brand-dot--faint"></div>
    <div class="brand-dot"></div>
    <svg class="card__waves" viewBox="0 0 567 342" preserveAspectRatio="none" aria-hidden="true">
      <path class="wave-blue" d="M0 148 C150 178 330 148 567 160 L567 186 C330 170 150 196 0 172Z"/>
      <path class="wave-green" d="M0 178 C150 192 300 138 567 158 L567 178 C300 156 150 206 0 194Z"/>
      <path class="wave-black" d="M0 190 C150 204 300 150 567 176 L567 342 L0 342Z"/>
    </svg>
    <h1 class="front-wordmark">Velora<br>Pixel<br>Outreach</h1>
  </section>

  <!-- Back, square corners -->
  <section class="card card--back card--top" aria-label="Card back">
    <div class="brand-dot"></div>
    <p class="back-wordmark">Velora<br>Pixel<br>Outreach</p>
    <svg class="card__waves" viewBox="0 0 567 342" preserveAspectRatio="none" aria-hidden="true">
      <path class="wave-blue" d="M0 148 C150 178 330 132 567 146 L567 170 C330 158 150 196 0 172Z"/>
      <path class="wave-green" d="M0 170 C150 192 300 140 567 150 L567 168 C300 158 150 206 0 190Z"/>
      <path class="wave-black" d="M0 186 C150 204 300 150 567 164 L567 342 L0 342Z"/>
    </svg>
    <div class="person">
      <p class="person__name"><span class="person__first">Dermot</span> <span class="person__last">Kalway</span></p>
      <p class="person__role">Online Marketing Strategist</p>
    </div>
    <ul class="contact-list">
      <li class="contact-list__item">
        <svg class="contact-icon" viewBox="0 0 20 20" aria-hidden="true"><rect width="20" height="20" fill="#29a9e0"/><circle cx="10" cy="10" r="6.5" fill="none" stroke="#fff" stroke-width="1.2"/><ellipse cx="10" cy="10" rx="2.8" ry="6.5" fill="none" stroke="#fff" stroke-width="1"/><path d="M3.5 10h13M5 6.5h10M5 13.5h10" stroke="#fff" stroke-width="1"/></svg>
        0492 158 620
      </li>
      <li class="contact-list__item">
        <svg class="contact-icon" viewBox="0 0 20 20" aria-hidden="true"><rect width="20" height="20" fill="#29a9e0"/><rect x="3.5" y="5.5" width="13" height="9" fill="#fff"/><path d="M3.5 5.5 10 11 16.5 5.5" fill="none" stroke="#29a9e0" stroke-width="1.2"/></svg>
        Dermot@VeloraPixelOutreach.example
      </li>
      <li class="contact-list__item">
        <svg class="contact-icon" viewBox="0 0 20 20" aria-hidden="true"><rect width="20" height="20" fill="#29a9e0"/></svg>
        in/dermotkalway
      </li>
    </ul>
  </section>

  <!-- Front, rounded corners -->
  <section class="card card--front card--bottom card--rounded" aria-label="Card front, rounded corners">
    <div class="brand-dot brand-dot--faint"></div>
    <div class="brand-dot"></div>
    <svg class="card__waves" viewBox="0 0 567 327" preserveAspectRatio="none" aria-hidden="true">
      <path class="wave-blue" d="M0 142 C150 172 330 142 567 150 L567 176 C330 162 150 188 0 164Z"/>
      <path class="wave-green" d="M0 170 C150 184 300 132 567 150 L567 170 C300 150 150 198 0 186Z"/>
      <path class="wave-black" d="M0 182 C150 196 300 144 567 168 L567 327 L0 327Z"/>
    </svg>
    <h1 class="front-wordmark">Velora<br>Pixel<br>Outreach</h1>
  </section>

  <!-- Back, rounded corners -->
  <section class="card card--back card--bottom card--rounded" aria-label="Card back, rounded corners">
    <div class="brand-dot"></div>
    <p class="back-wordmark">Velora<br>Pixel<br>Outreach</p>
    <svg class="card__waves" viewBox="0 0 567 327" preserveAspectRatio="none" aria-hidden="true">
      <path class="wave-blue" d="M0 142 C150 170 330 126 567 140 L567 164 C330 152 150 188 0 164Z"/>
      <path class="wave-green" d="M0 162 C150 184 300 134 567 144 L567 162 C300 152 150 198 0 182Z"/>
      <path class="wave-black" d="M0 178 C150 196 300 144 567 158 L567 327 L0 327Z"/>
    </svg>
    <div class="person">
      <p class="person__name"><span class="person__first">Dermot</span> <span class="person__last">Kalway</span></p>
      <p class="person__role">Online Marketing Strategist</p>
    </div>
    <ul class="contact-list">
      <li class="contact-list__item">
        <svg class="contact-icon" viewBox="0 0 20 20" aria-hidden="true"><rect width="20" height="20" fill="#29a9e0"/><circle cx="10" cy="10" r="6.5" fill="none" stroke="#fff" stroke-width="1.2"/><ellipse cx="10" cy="10" rx="2.8" ry="6.5" fill="none" stroke="#fff" stroke-width="1"/><path d="M3.5 10h13M5 6.5h10M5 13.5h10" stroke="#fff" stroke-width="1"/></svg>
        0492 158 620
      </li>
      <li class="contact-list__item">
        <svg class="contact-icon" viewBox="0 0 20 20" aria-hidden="true"><rect width="20" height="20" fill="#29a9e0"/><rect x="3.5" y="5.5" width="13" height="9" fill="#fff"/><path d="M3.5 5.5 10 11 16.5 5.5" fill="none" stroke="#29a9e0" stroke-width="1.2"/></svg>
        Dermot@VeloraPixelOutreach.example
      </li>
      <li class="contact-list__item">
        <svg class="contact-icon" viewBox="0 0 20 20" aria-hidden="true"><rect width="20" height="20" fill="#29a9e0"/></svg>
        in/dermotkalway
      </li>
    </ul>
  </section>

</main>
</body>
</html>
```